Re-style home page - eye-catching and unique design for social commerce website

We need a new concept design for BrinoKet's home page.
We don't want to make huge changes but creating a more professional and eye-catching style.

We need to look very serious like a professional services company and in the same time to look like a social network for e-commerce.

Our logo is very captive and you can use to creating something of harmonious.

This is a re-style and I'm excepted to see unique and fresh design like Glimmora.

Target Market(s)

e-commerce and social

Industry/Entity Type

Social

Number of Pages Required

1 page

Font styles to use
Serif
Sans Serif

Requirements
Must have
• An eye-catching result.
• Search bar with logo and Login How it works and business
• The slogan with login and signup.
• Footer links.
Nice to have
• I would like to open the home page and see only two clear ways:
• -Consumer
• --Search
• --The slogan
• --Login and Signup
• --How it works
• -Business
• --Go to Business area
• Background: City, Shopping.
Should not have
• Scrollbar style!

```html
<!DOCTYPE html>
<html lang="en">
<head>
<meta charset="UTF-8">
<title>BrinoKet – Home</title>
<link href="https://fonts.googleapis.com/css2?family=Open+Sans:wght@400;600;700&display=swap" rel="stylesheet">
<style>
  :root {
    --header-bg: #2f2f2f;
    --accent-red: #e0264f;
    --accent-red-dark: #d11d45;
    --accent-indigo: #5f5cc9;
    --subtitle-blue: #4a4f86;
    --social-blue: #4566a8;
    --card-bg: rgba(250, 250, 250, 0.93);
    --input-border: #cfcfcf;
    --text-dark: #2c2c2c;
    --text-muted: #6a6a6a;
    --nav-muted: #b9b9b9;
    --footer-bg: rgba(20, 20, 20, 0.72);
    --footer-text: #e2e2e2;
  }
  * { box-sizing: border-box; margin: 0; padding: 0; }
  html, body { width: 1200px; height: 658px; overflow: hidden; }
  body {
    position: relative;
    font-family: "Open Sans", Arial, sans-serif;
    color: var(--text-dark);
    background: #1a1a1a;
  }
  .city-backdrop {
    position: absolute; left: 0; top: 72px; width: 1200px; height: 586px;
    background:
      radial-gradient(ellipse 260px 140px at 130px 20px, rgba(255, 220, 150, 0.75), transparent 70%),
      radial-gradient(ellipse 500px 260px at 980px 420px, rgba(160, 110, 60, 0.35), transparent 70%),
      linear-gradient(180deg, #b79a6a 0%, #6d5a45 14%, #3e3a36 30%, #2d2a28 55%, #2a2622 80%, #1e1b19 100%);
  }
  .site-header {
    position: absolute; left: 0; top: 0; width: 1200px; height: 72px;
    background: var(--header-bg);
  }
  .brand {
    position: absolute; left: 100px; top: 18px;
    display: flex; align-items: center; gap: 8px;
    font-weight: 700; font-size: 27px; color: #ffffff; letter-spacing: -0.5px;
  }
  .brand-mark { width: 14px; height: 14px; background: var(--accent-red); border-radius: 50%; }
  .search-bar {
    position: absolute; left: 274px; top: 16px; width: 588px; height: 41px;
    background: #ffffff; border-radius: 3px;
  }
  .search-input {
    position: absolute; left: 20px; top: 11px;
    font-size: 13px; color: var(--text-muted);
  }
  .search-button {
    position: absolute; right: 4px; top: 4px; width: 71px; height: 33px;
    background: var(--accent-red); color: #fff; border-radius: 3px;
    font-size: 12px; font-weight: 600; display: flex; align-items: center; justify-content: center;
  }
  .main-nav {
    position: absolute; top: 27px; left: 0; font-size: 13px; font-weight: 600;
  }
  .main-nav a { position: absolute; white-space: nowrap; color: var(--nav-muted); text-decoration: none; }
  .main-nav .nav-login { left: 885px; color: #ffffff; }
  .main-nav .nav-how { left: 945px; }
  .main-nav .nav-business { left: 1049px; }
  .signup-card {
    position: absolute; left: 306px; top: 133px; width: 588px; height: 434px;
    background: var(--card-bg); border-radius: 3px; text-align: center;
  }
  .card-title {
    position: absolute; left: 0; top: 31px; width: 100%;
    font-size: 29px; font-weight: 700; color: var(--accent-red);
  }
  .card-subtitle {
    position: absolute; left: 0; top: 71px; width: 100%;
    font-size: 19px; font-weight: 600; color: var(--subtitle-blue);
  }
  .social-login {
    position: absolute; left: 205px; top: 109px; width: 178px; height: 34px;
    background: var(--social-blue); color: #fff; border-radius: 2px;
    font-size: 12px; font-weight: 700; display: flex; align-items: center; justify-content: center;
  }
  .divider-or {
    position: absolute; left: 0; top: 158px; width: 100%; font-size: 13px; color: var(--text-dark);
  }
  .field {
    position: absolute; left: 169px; width: 251px; height: 41px;
    background: #ffffff; border: 1px solid var(--input-border); border-radius: 3px;
    font-size: 12px; color: var(--text-muted); text-align: left; padding: 12px 16px;
  }
  .field-email { top: 192px; }
  .field-password { top: 243px; }
  .btn-signup {
    position: absolute; left: 169px; top: 295px; width: 251px; height: 41px;
    background: linear-gradient(180deg, var(--accent-red), var(--accent-red-dark));
    color: #fff; border-radius: 3px; font-size: 17px; font-weight: 600;
    display: flex; align-items: center; justify-content: center;
  }
  .btn-login {
    position: absolute; left: 255px; top: 348px; width: 79px; height: 36px;
    background: var(--accent-indigo); color: #fff; border-radius: 3px; font-size: 17px;
    display: flex; align-items: center; justify-content: center;
  }
  .card-note {
    position: absolute; left: 0; top: 396px; width: 100%; font-size: 11px; color: var(--text-dark);
  }
  .site-footer {
    position: absolute; left: 0; top: 612px; width: 1200px; height: 46px;
    background: var(--footer-bg);
    display: flex; align-items: center; justify-content: center;
    font-size: 11.5px; color: var(--footer-text);
  }
  .site-footer a { color: var(--footer-text); text-decoration: none; }
  .site-footer .sep { margin: 0 11px; }
</style>
</head>
<body>
  <div class="city-backdrop" role="img" aria-label="Evening city skyline with lit streets and shoppers walking in a mall"></div>

  <header class="site-header">
    <div class="brand"><span>BrinoKet</span><span class="brand-mark"></span></div>
    <div class="search-bar">
      <span class="search-input">Keyword</span>
      <span class="search-button">SEARCH</span>
    </div>
    <nav class="main-nav">
      <a class="nav-login" href="#">Login</a>
      <a class="nav-how" href="#">How it works</a>
      <a class="nav-business" href="#">Business</a>
    </nav>
  </header>

  <main class="signup-card">
    <h1 class="card-title">Shop Directly From Your Profile</h1>
    <p class="card-subtitle">Save your time. Live better.</p>
    <div class="social-login">Login with Friendnest</div>
    <p class="divider-or">Or</p>
    <div class="field field-email">Email</div>
    <div class="field field-password">Create a password</div>
    <div class="btn-signup">Sign up</div>
    <div class="btn-login">Log in</div>
    <p class="card-note">Aliquam ac elit vitae sapien elementum pulvinar eu eget leo</p>
  </main>

  <footer class="site-footer">
    <a href="#">About</a><span class="sep">|</span>
    <a href="#">Blog</a><span class="sep">|</span>
    <a href="#">Businesses</a><span class="sep">|</span>
    <a href="#">Terms and Conditions</a><span class="sep">|</span>
    <a href="#">Help</a><span class="sep">|</span>
    <a href="#">Pocket App</a><span class="sep">|</span>
    <a href="#">Tablet App</a><span class="sep">|</span>
    <span>Copyright ©&nbsp; 2015&nbsp; BrinoKet.&nbsp; All rights reserved.</span>
  </footer>
</body>
</html>
```